Garlic Farm for Farm Sales/Restaurant sales

Need a professional, but appealing to agriculture world. We are selling 27 kinds of Organic Garlic from a farm in Simla,CO. I have uploaded logo and business information-we are going to need a template, because I will need to use it for four separate people.
-We are trying to appeal to Farm to table restaurants
-As well as growers/farmers

Target Market(s)

Agriculture Sales/Restaurants-Organic

Industry/Entity Type

Agriculture

Contact Information for Business Card

Want it to look more unique then your average kelto stock card- I want it to look amazing

Font styles to use
Sans Serif

Colors
0455a3
ec1f27
fbed22
ffffff

Requirements
Must have
• Just be creative
Nice to have
• Colorful
Should not have
• plain

```html
<!DOCTYPE html>
<html lang="en">
<head>
<meta charset="utf-8">
<title>Ridgeline Garlic Co. — Business Card</title>
<link rel="stylesheet" href="https://fonts.googleapis.com/css2?family=Kalam:wght@400;700&family=Montserrat:wght@300;400;700&display=swap">
<style>
  :root {
    --navy: #17325e;
    --red: #c8213a;
    --coral: #e0563e;
    --yellow: #f5c518;
    --white: #ffffff;
    --ink: #4a5468;
    --rule: #d9dce2;
    --stage: #ecebe7;
  }
  * { box-sizing: border-box; margin: 0; padding: 0; }
  html, body { width: 1200px; height: 950px; overflow: hidden; }
  body {
    background: var(--stage);
    position: relative;
    font-family: "Montserrat", sans-serif;
  }
  .card {
    position: absolute;
    width: 620px;
    height: 355px;
    border-radius: 22px;
    overflow: hidden;
    box-shadow: 0 8px 24px rgba(20, 30, 50, 0.18);
  }

  /* Front */
  .card-front { left: 70px; top: 80px; background: var(--white); }
  .front-brand {
    position: absolute; left: 0; top: 0; width: 300px; height: 100%;
    display: flex; align-items: center; justify-content: center; gap: 12px;
  }
  .brand-dot { width: 46px; height: 46px; border-radius: 50%; background: var(--red); flex: none; }
  .brand-name {
    font-weight: 700; font-size: 24px; color: var(--navy);
    text-transform: lowercase; line-height: 1.05;
  }
  .front-divider {
    position: absolute; left: 300px; top: 40px; bottom: 40px;
    width: 1px; background: var(--rule);
  }
  .front-details {
    position: absolute; left: 335px; top: 0; right: 30px; height: 100%;
    display: flex; flex-direction: column; justify-content: center;
  }
  .person-name { font-family: "Kalam", cursive; font-size: 26px; color: var(--navy); line-height: 1; }
  .person-title { font-family: "Kalam", cursive; font-size: 18px; color: var(--red); margin-bottom: 18px; }
  .address, .contact { font-weight: 300; font-size: 14px; color: var(--ink); line-height: 1.5; }
  .address { margin-bottom: 14px; }
  .contact { display: flex; align-items: center; gap: 8px; }
  .contact svg { width: 14px; height: 14px; flex: none; }
  .front-edge {
    position: absolute; right: 0; top: 0; bottom: 0; width: 10px;
    background: linear-gradient(to right, var(--red) 0 30%, var(--yellow) 30% 60%, var(--navy) 60% 100%);
  }

  /* Back */
  .card-back { left: 510px; top: 510px; background: var(--navy); }
  .back-web {
    position: absolute; left: 26px; top: 20px;
    font-weight: 300; font-size: 14px; color: var(--white); letter-spacing: 0.5px;
  }
  .back-disc {
    position: absolute; left: 60px; top: 55px; width: 240px; height: 240px;
    border-radius: 50%; background: var(--red);
  }
  .back-brand {
    position: absolute; right: 34px; bottom: 44px;
    font-weight: 700; font-size: 34px; color: var(--white);
    text-transform: lowercase; text-align: right; line-height: 1.05;
  }
</style>
</head>
<body>

  <section class="card card-front" aria-label="Business card front">
    <div class="front-brand">
      <span class="brand-dot"></span>
      <span class="brand-name">ridgeline<br>garlic co.</span>
    </div>
    <div class="front-divider"></div>
    <div class="front-details">
      <p class="person-name">Dana Hollis</p>
      <p class="person-title">CEO/Founder</p>
      <p class="address">P.O. Box 12 Pinefall<br>CO 80999</p>
      <p class="contact">
        <svg viewBox="0 0 24 24" aria-hidden="true"><path fill="var(--navy)" d="M6.6 10.8a15 15 0 0 0 6.6 6.6l2.2-2.2a1 1 0 0 1 1-.25 11.4 11.4 0 0 0 3.6.57 1 1 0 0 1 1 1V20a1 1 0 0 1-1 1A17 17 0 0 1 3 4a1 1 0 0 1 1-1h3.5a1 1 0 0 1 1 1c0 1.25.2 2.45.57 3.57a1 1 0 0 1-.25 1z"/></svg>
        555-014-2290
      </p>
      <p class="contact">
        <svg viewBox="0 0 24 24" aria-hidden="true"><rect x="2" y="5" width="20" height="14" rx="1.5" fill="none" stroke="var(--navy)" stroke-width="2"/><path d="M3 6l9 7 9-7" fill="none" stroke="var(--navy)" stroke-width="2"/></svg>
        dana@ridgelinegarlic.com
      </p>
    </div>
    <div class="front-edge"></div>
  </section>

  <section class="card card-back" aria-label="Business card back">
    <p class="back-web">www.ridgelinegarlic.com</p>
    <div class="back-disc"></div>
    <p class="back-brand">ridgeline<br>garlic co.</p>
  </section>

</body>
</html>
```